All-Natural Head Lice Removal company

I need a business card with my pre-existing logo. We are a new company located in Portland Oregon that goes into peoples homes to help with head lice removal. My products and approach are all- natural and also will be around children.On my current logo we used Teal Bl and the color Green. I am open to new ideas just want it simple and creative

Target Market(s)

my biggest market is families of school aged children

Industry/Entity Type

Business

Contact Information for Business Card

see upload for details from previous business card

Font styles to use
Serif

Colors
33a6d7
9bcb3b
f37122

Requirements
Must have
• Basic information/ logo put into a creative format that is catching to the eye
Nice to have
• creative

```html
<!DOCTYPE html>
<html lang="en">
<head>
<meta charset="utf-8">
<title>Nit Scout – Business Card</title>
<link rel="stylesheet" href="https://fonts.googleapis.com/css2?family=Comic+Neue:wght@400;700&display=swap">
<style>
  :root {
    --page-bg: #d8d5d1;
    --frost: #eceeeb;
    --frost-edge: #dfe2de;
    --leaf-dark: #3a8f25;
    --leaf: #4fae33;
    --leaf-light: #62bf45;
    --teal: #33a6d7;
    --ink: #1d1d1d;
    --name-green: #cde9a8;
    --contact-green: #bfe398;
    --owner: #e9f3e0;
  }
  * { box-sizing: border-box; margin: 0; padding: 0; }
  html, body {
    width: 1200px;
    height: 969px;
    overflow: hidden;
    background: var(--page-bg);
  }
  .canvas {
    position: relative;
    width: 1200px;
    height: 969px;
  }
  .card {
    position: absolute;
    left: 80px;
    top: 188px;
    width: 1040px;
    height: 592px;
    border-radius: 34px;
    overflow: hidden;
    background: linear-gradient(180deg, var(--frost) 0%, var(--frost-edge) 100%);
    box-shadow: 0 10px 30px rgba(0,0,0,0.18);
    font-family: "Comic Neue", "Comic Sans MS", cursive;
  }
  .card__green {
    position: absolute;
    inset: 0;
    background: linear-gradient(90deg,
      rgba(79,174,51,0) 40%,
      var(--leaf-dark) 54%,
      var(--leaf) 75%,
      var(--leaf-light) 100%);
  }
  .card__illustration {
    position: absolute;
    left: 470px;
    top: 0;
    width: 300px;
    height: 592px;
    border-radius: 150px 150px 40px 40px;
    background: radial-gradient(ellipse at 50% 30%,
      rgba(51,166,215,0.55) 0%,
      rgba(51,166,215,0.35) 35%,
      rgba(30,40,40,0.25) 70%,
      rgba(30,40,40,0) 100%);
  }
  .brand {
    position: absolute;
    left: 56px;
    top: 90px;
    display: flex;
    align-items: center;
    gap: 18px;
  }
  .brand__dot {
    width: 92px;
    height: 92px;
    border-radius: 50%;
    background: var(--leaf);
  }
  .brand__name {
    font-size: 66px;
    font-weight: 700;
    color: var(--ink);
    line-height: 1;
  }
  .tagline {
    position: absolute;
    left: 62px;
    top: 398px;
    font-size: 29px;
    line-height: 36px;
    color: var(--ink);
  }
  .social-square {
    position: absolute;
    right: 66px;
    top: 59px;
    width: 84px;
    height: 84px;
    border-radius: 12px;
    background: #3b5998;
  }
  .contact {
    position: absolute;
    right: 54px;
    top: 320px;
    text-align: right;
  }
  .contact__name {
    font-size: 37px;
    font-weight: 700;
    color: var(--name-green);
    line-height: 48px;
    letter-spacing: 0.5px;
  }
  .contact__role {
    font-size: 28px;
    color: var(--owner);
    line-height: 40px;
    margin-bottom: 24px;
  }
  .contact__line {
    font-size: 28px;
    color: var(--contact-green);
    line-height: 41px;
  }
</style>
</head>
<body>
<div class="canvas">
  <div class="card">
    <div class="card__green"></div>
    <div class="card__illustration" role="img" aria-label="Large cartoon magnifying glass with an eye looking through the lens"></div>

    <div class="brand">
      <span class="brand__dot"></span>
      <span class="brand__name">Nit Scout</span>
    </div>

    <p class="tagline">
      Try Nit Scout Today and<br>
      Be Lice Free Tomorrow!<br>
      All Natural In-Home Lice<br>
      Removal Services
    </p>

    <div class="social-square" aria-label="Social media page"></div>

    <div class="contact">
      <p class="contact__name">Dana Whitfield</p>
      <p class="contact__role">Owner</p>
      <p class="contact__line">1-855-555-NITS (6487)</p>
      <p class="contact__line">dana@nitscout.com</p>
      <p class="contact__line">www.nitscout.com</p>
    </div>
  </div>
</div>
</body>
</html>
```